Indonesian B2B Company (Bawo Ingredients) - Stationery Design

Bawo Ingredients needs a corporate, bold and professional-looking stationery design.

Bawo Ingredients is a new Indonesian company manufacturing, marketing and distributing various ingredients / raw materials such as flavours, fragrance, colours, sweeteners, preservatives for the food & beverage, pharmaceutical, personal care and other household goods industries.

It is a business to business (B2B) company as we supply various natural and synthetic raw materials to various consumer goods manufacturers. We therefore need a logo/identity with corporate and industrial style.

Bawo Ingredients is a startup company which belongs to a larger Tunas Mekar group of companies (http://tunasmekar.examplebiz.net/about) that focuses in the mining, petroleum and energy businesses. Bawo Ingredients would like to focus in providing good quality, safe, reliable and affordable ingredients for the industries. Our tagline is "Trusted Inputs for Industry"
Updates

We have updated some information including our requirements and contact details to be shown in the stationery. Please check the project brief.

Regards,

Bawo Ingredients

Target Market(s)

Manufacturers of food & beverages, personal care, pharmaceutical and other FMCG factories.

Industry/Entity Type

Business

Requirements
Must have
• Smart, professional and corporate touches in the stationery designs. We require designs for:
1. Letterhead
2. Envelope (with and without window)
3. Name card
4. Powerpoint presentation template
5. CD label
6. Small memo / with compliments card

Contact details:

Company name:
PT Bawo Ingredients

Address:
Ruko Puri Lestari Selatan, Blok F07 no: 11-12
Sunter Jaya Utara, 14350
Indonesia

Tel:+62 21 638 2097
Fax:+62 21 638 2096
Email: info@bawo-ingredients.co.id
Website: www.bawogroup.id

```html
<!DOCTYPE html>
<html lang="en">
<head>
<meta charset="utf-8">
<title>Bawo Ingredients — Presentation Template</title>
<link rel="stylesheet" href="https://fonts.googleapis.com/css2?family=Open+Sans:wght@400;600;700&display=swap">
<style>
  :root {
    --red: #d01f2b;
    --red-deep: #a9131d;
    --red-dark: #7a0b12;
    --orange: #f5a93b;
    --white: #ffffff;
    --grey-text: #8a8a8a;
    --stage: #e9e7e4;
    --font: "Open Sans", Arial, sans-serif;
  }
  * { margin: 0; padding: 0; box-sizing: border-box; }
  html, body { width: 1200px; height: 900px; overflow: hidden; }
  body { background: var(--stage); font-family: var(--font); position: relative; }

  .slide {
    position: absolute;
    width: 535px;
    height: 402px;
    background: var(--white);
    overflow: hidden;
    box-shadow: 0 3px 10px rgba(0,0,0,0.18);
  }
  .slide--title-light { left: 50px;  top: 35px; }
  .slide--content-a   { left: 610px; top: 35px; }
  .slide--title-red   { left: 50px;  top: 474px; }
  .slide--content-b   { left: 610px; top: 474px; }

  .red-field {
    position: absolute; left: 0; right: 0; bottom: 0;
    background: linear-gradient(135deg, var(--red) 0%, var(--red-deep) 70%, var(--red-dark) 100%);
  }
  .slide--title-light .red-field { top: 170px; }
  .slide--title-red .red-field { top: 0; }

  .brand {
    position: absolute; left: 28px; top: 80px;
    display: flex; flex-direction: column;
  }
  .brand__mark {
    width: 24px; height: 24px; border-radius: 50%;
    background: var(--red); margin-bottom: 10px;
  }
  .slide--title-red .brand__mark { background: var(--white); }
  .brand__name {
    font-weight: 600; font-size: 21px; letter-spacing: -0.3px; line-height: 1.1;
    color: var(--red);
  }
  .slide--title-red .brand__name { color: var(--white); }
  .brand__tagline {
    font-weight: 600; font-size: 10px; color: var(--grey-text); margin-top: 3px;
  }
  .slide--title-red .brand__tagline { color: var(--white); }

  .divider-light {
    position: absolute; left: 0; top: 176px; width: 420px; height: 1px;
    background: linear-gradient(90deg, rgba(255,255,255,0.55), rgba(255,255,255,0));
  }

  .title-block { position: absolute; left: 30px; top: 194px; color: var(--white); }
  .title-block__heading { font-weight: 700; font-size: 21px; line-height: 1.25; }
  .title-block__sub { font-weight: 400; font-size: 15px; line-height: 1.3; margin-top: 2px; }

  .slide-heading {
    position: absolute; left: 40px; top: 22px;
    font-weight: 700; font-size: 16px; color: var(--red);
  }
  .slide-rule {
    position: absolute; left: 0; top: 57px; width: 480px; height: 1px;
    background: linear-gradient(90deg, rgba(208,31,43,0) 0%, #e2a59a 15%, #f0d3b8 70%, rgba(240,211,184,0) 100%);
  }

  .footer-band { position: absolute; left: 0; bottom: 0; width: 535px; height: 44px; }

  .site-url {
    position: absolute; left: 15px; bottom: 8px;
    font-size: 8px; font-weight: 400; color: var(--white); letter-spacing: 0.3px;
  }
</style>
</head>
<body>

  <section class="slide slide--title-light">
    <div class="red-field"></div>
    <div class="brand">
      <span class="brand__mark"></span>
      <span class="brand__name">Bawo Ingredients</span>
      <span class="brand__tagline">Trusted Inputs for Industry</span>
    </div>
    <div class="title-block">
      <h1 class="title-block__heading">Lorem Ipsum Dolor sit Amet</h1>
      <p class="title-block__sub">Lorem Ipsum Dolor sit Amet</p>
    </div>
    <svg class="footer-band" viewBox="0 0 535 44" aria-hidden="true">
      <rect x="0" y="18" width="535" height="26" fill="var(--red-dark)"/>
      <rect x="0" y="14" width="535" height="3" fill="var(--orange)"/>
      <rect x="400" y="18" width="135" height="26" fill="var(--orange)"/>
    </svg>
    <span class="site-url">www.bawogroup.id</span>
  </section>

  <section class="slide slide--content-a">
    <h2 class="slide-heading">Lorem Ipsum Dolor sit Amet</h2>
    <div class="slide-rule"></div>
    <svg class="footer-band" viewBox="0 0 535 44" aria-hidden="true">
      <rect x="0" y="18" width="535" height="26" fill="var(--red)"/>
      <rect x="0" y="14" width="535" height="3" fill="var(--orange)"/>
      <rect x="400" y="18" width="135" height="26" fill="var(--red-dark)"/>
    </svg>
  </section>

  <section class="slide slide--title-red">
    <div class="red-field"></div>
    <div class="brand">
      <span class="brand__mark"></span>
      <span class="brand__name">Bawo Ingredients</span>
      <span class="brand__tagline">Trusted Inputs for Industry</span>
    </div>
    <div class="divider-light"></div>
    <div class="title-block">
      <h1 class="title-block__heading">Lorem Ipsum Dolor sit Amet</h1>
      <p class="title-block__sub">Lorem Ipsum Dolor sit Amet</p>
    </div>
    <svg class="footer-band" viewBox="0 0 535 44" aria-hidden="true">
      <rect x="0" y="18" width="535" height="26" fill="var(--red-dark)"/>
      <rect x="0" y="14" width="535" height="3" fill="var(--orange)"/>
      <rect x="400" y="18" width="135" height="26" fill="var(--orange)"/>
    </svg>
    <span class="site-url">www.bawogroup.id</span>
  </section>

  <section class="slide slide--content-b">
    <h2 class="slide-heading">Lorem Ipsum Dolor sit Amet</h2>
    <div class="slide-rule"></div>
    <svg class="footer-band" viewBox="0 0 535 44" aria-hidden="true">
      <rect x="0" y="18" width="535" height="26" fill="var(--red)"/>
      <rect x="0" y="14" width="535" height="3" fill="var(--orange)"/>
      <rect x="400" y="18" width="135" height="26" fill="var(--red-dark)"/>
    </svg>
  </section>

</body>
</html>
```